Coffeeshop menu for filter tip

We want to have a cannabis (coffeeshop) menu in the size 25mm wide x 60mm wide. Some examples attached.

it must have the following text:
Menu

WEED p/g
Oblivane €16
Cloudplum €14
Tide Runner €14
Quincefig €16
Mega Marsh €14
Grey Heron €14

HASH p/g
Tashar Amber €12
Pebble Frost€11
Lime Dunes €14
Ash Petal €10

Target Market(s)

tourist in Amsterdam

Requirements
Nice to have
• cannabis sign leaf
• No Cigarettes allowed symbol

```html
<!DOCTYPE html>
<html lang="en">
<head>
<meta charset="utf-8">
<title>Coffeeshop Menu – Filter Tip</title>
<link rel="stylesheet" href="https://fonts.googleapis.com/css2?family=Anton&family=Ewert&family=Rye&family=Stardos+Stencil:wght@700&family=Kaushan+Script&family=Mystery+Quest&family=Aladin&family=UnifrakturMaguntia&family=Pirata+One&family=Creepster&display=swap">
<style>
  :root {
    --page: #ffffff;
    --leaf-green: #1e8c3e;
    --leaf-light: #36ad57;
    --frame-gold: #efdc98;
    --frame-gold-deep: #c9a85a;
    --panel-red: #8e1e22;
    --panel-brown: #3b1c0f;
    --title-green: #2fb04a;
    --menu-white: #fbf6ea;
  }
  html, body {
    margin: 0;
    width: 706px;
    height: 1200px;
    overflow: hidden;
    background: var(--page);
  }
  .menu-card {
    position: absolute;
    left: 156px;
    top: 134px;
    width: 398px;
    height: 952px;
  }
  .leaf-backdrop {
    position: absolute;
    inset: 0;
    background: radial-gradient(circle at 50% 50%, var(--leaf-light) 0%, var(--leaf-green) 70%);
  }
  .scroll-frame {
    position: absolute;
    left: 13px;
    width: 372px;
    background: linear-gradient(135deg, var(--frame-gold) 0%, var(--frame-gold-deep) 50%, var(--frame-gold) 100%);
    border-radius: 14px;
  }
  .scroll-frame--weed { top: 10px; height: 537px; }
  .scroll-frame--hash { top: 522px; height: 418px; }
  .menu-panel {
    position: absolute;
    left: 49px;
    width: 303px;
    background: radial-gradient(ellipse at 50% 55%, var(--panel-red) 0%, var(--panel-brown) 85%);
    color: var(--menu-white);
    box-sizing: border-box;
    padding: 0 20px 0 22px;
  }
  .menu-panel--weed { top: 63px; height: 443px; }
  .menu-panel--hash { top: 571px; height: 325px; }
  .menu-title {
    margin: 0;
    text-align: center;
    font-family: "Anton", Impact, sans-serif;
    font-size: 48px;
    color: var(--title-green);
    letter-spacing: 1px;
    line-height: 1;
  }
  .menu-title small { font-size: 28px; }
  .menu-panel--weed .menu-title { margin-top: 50px; margin-bottom: 8px; }
  .menu-panel--hash .menu-title { margin-top: 42px; margin-bottom: 10px; }
  .menu-list { list-style: none; margin: 0; padding: 0; }
  .menu-item {
    display: flex;
    justify-content: space-between;
    align-items: baseline;
    height: 46px;
    font-size: 29px;
    line-height: 46px;
    white-space: nowrap;
  }
  .menu-panel--hash .menu-item { height: 50px; line-height: 50px; }
  .strain-oblivane { font-family: "Ewert", serif; font-size: 24px; }
  .strain-cloudplum { font-family: "Rye", serif; font-size: 25px; }
  .strain-tiderunner { font-family: "Stardos Stencil", serif; font-weight: 700; }
  .strain-quincefig { font-family: "Kaushan Script", cursive; }
  .strain-megamarsh { font-family: "Mystery Quest", cursive; }
  .strain-greyheron { font-family: "Aladin", cursive; }
  .strain-tashar { font-family: "UnifrakturMaguntia", serif; font-size: 28px; }
  .strain-pebble { font-family: "Pirata One", serif; }
  .strain-lime { font-family: "Rye", serif; font-size: 24px; }
  .strain-ash { font-family: "Creepster", cursive; letter-spacing: 1px; }
</style>
</head>
<body>
  <main class="menu-card">
    <div class="leaf-backdrop" role="img" aria-label="Pattern of green cannabis leaves"></div>

    <div class="scroll-frame scroll-frame--weed" role="img" aria-label="Gold baroque scrollwork frame around the weed menu"></div>
    <div class="scroll-frame scroll-frame--hash" role="img" aria-label="Gold baroque scrollwork frame around the hash menu"></div>

    <section class="menu-panel menu-panel--weed">
      <h2 class="menu-title">WEED <small>p/g</small></h2>
      <ul class="menu-list">
        <li class="menu-item strain-oblivane"><span>Oblivane</span><span>€16</span></li>
        <li class="menu-item strain-cloudplum"><span>Cloudplum</span><span>€14</span></li>
        <li class="menu-item strain-tiderunner"><span>TIDE RUNNER</span><span>€14</span></li>
        <li class="menu-item strain-quincefig"><span>Quincefig</span><span>€16</span></li>
        <li class="menu-item strain-megamarsh"><span>Mega Marsh</span><span>€14</span></li>
        <li class="menu-item strain-greyheron"><span>Grey Heron</span><span>€14</span></li>
      </ul>
    </section>

    <section class="menu-panel menu-panel--hash">
      <h2 class="menu-title">HASH <small>p/g</small></h2>
      <ul class="menu-list">
        <li class="menu-item strain-tashar"><span>Tashar Amber</span><span>€12</span></li>
        <li class="menu-item strain-pebble"><span>Pebble Frost</span><span>€11</span></li>
        <li class="menu-item strain-lime"><span>Lime Dunes</span><span>€14</span></li>
        <li class="menu-item strain-ash"><span>ASH PETAL</span><span>€10</span></li>
      </ul>
    </section>
  </main>
</body>
</html>
```